BRISK requires an exciting new business card

New business card required for BRISK. We are a new market research consultancy and want our brand to be approachable and be contemporary/modern, bold, uncomplicated/simple, and use friendly and easy to read fonts.

A draft website front page is attached to give you a feel (the pictures will be improved over the coming days).

The business card will be printed on 600gsm card, full colour both sides. The card is unique in that it allows one of four colours to be placed within the seam of the card (see http://uk.prentvo.com/products/gilt/business-cards.html)

The logo has been designed in yellow on white, white on yellow, yellow on black and black on yellow - please select whichever you feel most appropriate from the attached document (please use the versions with the tagline). I think my preference is yellow on white for the front, and then yellow or black as the dominant colour on the back.

Telephone numbers will be given next week as they are now being finalised.

Thanks

Target Market(s)

Professionals in large corporates, such as Marketing Managers at Grovane, Fizzaro Pop, Delmarco etc.

Industry/Entity Type

Market Research

Requirements
Must have
• Dana Pruitt QPMR
brisk
Level 4, 37 Quarrell St
Surrey Hills
NSW 2010
Tel: 02 XXXX XXXX
Mob: XXXX XXXXXX
Email: dana@briskqr.com.au
Web: www.briskqr.com.au

```html
<!DOCTYPE html>
<html lang="en">
<head>
<meta charset="utf-8">
<title>brisk – business card</title>
<link rel="stylesheet" href="https://fonts.googleapis.com/css2?family=Source+Sans+3:ital,wght@0,400;0,700;1,400;1,700&display=swap">
<style>
  :root {
    --yellow: #fccd0a;
    --charcoal: #434345;
    --white: #ffffff;
    --backdrop: #b48662;
    --label: #1e1611;
    --ink: #2b2b2b;
  }
  * { margin: 0; padding: 0; box-sizing: border-box; }
  html, body { width: 1200px; height: 788px; overflow: hidden; }
  body {
    position: relative;
    background: var(--backdrop);
    font-family: "Source Sans 3", Arial, sans-serif;
  }
  .view-label {
    position: absolute;
    width: 525px;
    text-align: center;
    font-size: 21px;
    color: var(--label);
  }
  .card {
    position: absolute;
    width: 525px;
    height: 298px;
    border-radius: 22px;
    overflow: hidden;
    box-shadow: 0 6px 14px rgba(0,0,0,.35);
  }
  .card--white { background: var(--white); }
  .card--charcoal { background: var(--charcoal); }
  .card--yellow { background: var(--yellow); }

  .wordmark {
    position: absolute;
    left: 0; right: 0;
    display: flex;
    flex-direction: column;
    align-items: center;
  }
  .wordmark__name {
    font-family: "Source Sans 3", Arial, sans-serif;
    font-weight: 700;
    line-height: 1;
  }
  .wordmark__tagline { line-height: 1; margin-top: 4px; }

  .wordmark--front { top: 34px; }
  .wordmark--front .wordmark__name { font-size: 82px; color: var(--yellow); }
  .wordmark--front .wordmark__tagline { font-size: 14px; color: var(--ink); }

  .wordmark--back { top: 70px; }
  .wordmark--back .wordmark__name { font-size: 120px; }
  .wordmark--back .wordmark__tagline { font-size: 19px; }
  .on-white .wordmark__name, .on-yellow .wordmark__name,
  .on-white .wordmark__tagline, .on-yellow .wordmark__tagline { color: var(--charcoal); }
  .on-charcoal .wordmark__name, .on-charcoal .wordmark__tagline { color: var(--yellow); }

  .bands { position: absolute; left: 0; top: 163px; width: 525px; height: 64px; }
  .bands .band-yellow { fill: var(--yellow); }
  .bands .band-charcoal { fill: var(--charcoal); }

  .holder { position: absolute; left: 61px; top: 176px; color: var(--ink); }
  .holder__name { font-size: 17px; font-weight: 700; line-height: 1.1; }
  .holder__title { font-size: 12px; font-style: italic; color: var(--charcoal); }

  .phones {
    position: absolute; right: 62px; top: 177px;
    text-align: right; color: var(--white); font-size: 13px; line-height: 19px;
  }
  .phones b { font-style: italic; }

  .contact {
    position: absolute; left: 0; right: 0; top: 241px;
    text-align: center; color: var(--ink); font-size: 15px; line-height: 20px;
  }
  .contact b { font-style: italic; }
  .contact .sep { margin: 0 6px; }
</style>
</head>
<body>
  <div class="view-label" style="left:55px; top:33px;">Front</div>
  <div class="view-label" style="left:622px; top:33px;">Back - 1</div>
  <div class="view-label" style="left:55px; top:403px;">Back - 2</div>
  <div class="view-label" style="left:622px; top:403px;">Back - 3</div>

  <section class="card card--white card-front" style="left:55px; top:75px;">
    <div class="wordmark wordmark--front">
      <span class="wordmark__name">brisk</span>
      <span class="wordmark__tagline">clear market insight</span>
    </div>

    <svg class="bands" viewBox="0 0 525 64" aria-hidden="true">
      <polygon class="band-yellow" points="0,0 267,0 203,64 0,64"/>
      <polygon class="band-charcoal" points="282,0 525,0 525,64 218,64"/>
    </svg>

    <div class="holder">
      <div class="holder__name">Dana Pruitt</div>
      <div class="holder__title">QPMR</div>
    </div>

    <div class="phones">
      <div><b>p</b> : 02 XXXX XXXX</div>
      <div><b>c</b> : XXXX XXXXXX</div>
    </div>

    <div class="contact">
      <div><b>e</b> : dana@briskqr.com.au<span class="sep">|</span><b>w</b> : www.briskqr.com.au</div>
      <div>brisk Level 4, 37 Quarrell St, Ferndale Park, NSW 2188</div>
    </div>
  </section>

  <section class="card card--white on-white" style="left:622px; top:75px;">
    <div class="wordmark wordmark--back">
      <span class="wordmark__name">brisk</span>
      <span class="wordmark__tagline">clear market insight</span>
    </div>
  </section>

  <section class="card card--charcoal on-charcoal" style="left:55px; top:446px;">
    <div class="wordmark wordmark--back">
      <span class="wordmark__name">brisk</span>
      <span class="wordmark__tagline">clear market insight</span>
    </div>
  </section>

  <section class="card card--yellow on-yellow" style="left:622px; top:441px;">
    <div class="wordmark wordmark--back">
      <span class="wordmark__name">brisk</span>
      <span class="wordmark__tagline">clear market insight</span>
    </div>
  </section>
</body>
</html>
```